Cover for Lanterns Along the Quiet Shore of Being

Cover for a book that describes everything that happens to a person, from pre-birth life plans through growing in compassion and wisdom to death and living in the afterlife. The information is revealed in messages from people living in the life after this life. The title is Lessons Gathered From Every Season of Your Existence: Shared by Voices Dwelling Beyond the Veil. Author is T. Wesley Prandt. Book size is 6 by 9.

Target Market(s)

General

Font styles to use
Serif

```html
<!DOCTYPE html>
<html lang="en">
<head>
<meta charset="utf-8">
<title>Lessons Gathered From Every Season of Your Existence — Book Cover</title>
<link rel="stylesheet" href="https://fonts.googleapis.com/css2?family=Playfair+Display:wght@700;900&family=Tinos&display=swap">
<style>
  :root {
    --page-bg: #ffffff;
    --navy: #2e2a66;
    --deep-teal: #1f6f86;
    --teal: #1a8d9b;
    --pink: #ee6d9c;
    --peach: #f4a07f;
    --sun: #fdd640;
    --title-white: #ffffff;
    --title-shadow: #3a1f55;
    --rule-white: #ffffff;
    --author-gold: #f2b35c;
  }
  * { margin: 0; padding: 0; box-sizing: border-box; }
  html, body {
    width: 1200px;
    height: 1200px;
    overflow: hidden;
    background: var(--page-bg);
  }
  .canvas {
    position: relative;
    width: 1200px;
    height: 1200px;
  }
  .book-cover {
    position: absolute;
    left: 260px;
    top: 90px;
    width: 680px;
    height: 1020px;
    overflow: hidden;
    background: var(--navy);
  }
  .cover-art {
    position: absolute;
    inset: 0;
    width: 100%;
    height: 100%;
  }
  .title-rule {
    position: absolute;
    left: 549px;
    top: 219px;
    width: 3px;
    height: 652px;
    background: var(--rule-white);
  }
  .cover-title {
    position: absolute;
    right: 147px;
    top: 212px;
    width: 460px;
    font-family: "Playfair Display", "Bodoni Moda", serif;
    font-weight: 900;
    font-size: 62px;
    line-height: 82px;
    letter-spacing: -0.5px;
    text-align: right;
    color: var(--title-white);
    text-shadow: 3px 3px 0 var(--title-shadow);
  }
  .cover-title span { display: block; }
  .cover-subtitle {
    position: absolute;
    right: 150px;
    top: 786px;
    width: 380px;
    font-family: "Tinos", "Times New Roman", serif;
    font-size: 27px;
    line-height: 44px;
    text-align: left;
    color: var(--title-white);
  }
  .cover-subtitle span { display: block; }
  .cover-author {
    position: absolute;
    right: 128px;
    top: 900px;
    font-family: "Playfair Display", "Bodoni Moda", serif;
    font-weight: 700;
    font-size: 33px;
    letter-spacing: 0.5px;
    text-transform: uppercase;
    color: var(--author-gold);
    white-space: nowrap;
  }
</style>
</head>
<body>
  <main class="canvas">
    <section class="book-cover">
      <svg class="cover-art" viewBox="0 0 680 1020" preserveAspectRatio="none" role="img" aria-label="Abstract painted spiral swirling from a glowing yellow centre through pink and teal bands into a deep navy field">
        <defs>
          <linearGradient id="coverBase" x1="0" y1="0" x2="1" y2="1">
            <stop offset="0" stop-color="#2e2a66"/>
            <stop offset="0.6" stop-color="#2c4c7f"/>
            <stop offset="1" stop-color="#1a8d9b"/>
          </linearGradient>
          <radialGradient id="spiralGlow" cx="0.78" cy="0.12" r="0.78" fx="0.82" fy="0.1">
            <stop offset="0" stop-color="#fdd640"/>
            <stop offset="0.28" stop-color="#f4a07f"/>
            <stop offset="0.55" stop-color="#ee6d9c"/>
            <stop offset="0.78" stop-color="#c9608f" stop-opacity="0.8"/>
            <stop offset="1" stop-color="#2e2a66" stop-opacity="0"/>
          </radialGradient>
        </defs>
        <rect width="680" height="1020" fill="url(#coverBase)"/>
        <rect width="680" height="1020" fill="url(#spiralGlow)"/>
      </svg>

      <div class="title-rule"></div>

      <h1 class="cover-title">
        <span>Lessons</span>
        <span>Gathered</span>
        <span>From Every</span>
        <span>Season of</span>
        <span>Your</span>
        <span>Existence:</span>
      </h1>

      <p class="cover-subtitle">
        <span>Shared by Voices Dwelling</span>
        <span>Beyond the Veil</span>
      </p>

      <p class="cover-author">T. Wesley Prandt</p>
    </section>
  </main>
</body>
</html>
```